Mira Bloom Fitness Coaching Project

I am a personal trainer based in London. My services include one-on-one PT sessions, bootcamps.
I would like the design to be minimalistic. With light colours: white, pink, purple.
I specialise in weight loss, flexibility, mobility.

Tessa Brogan
Personal Trainer
Email: tessa.brogan@quellmail.com
tel: 07700218493
Instagram: Mira Bloom

Target Market(s)

adults, mostly females (age 18-50).

Industry/Entity Type

Fitness

Contact Information for Business Card

Tessa Brogan
Personal Trainer
tel: 07700218493
Instagram: Mira Bloom

Font styles to use
Serif

Colors
eea4c8
fbd4d5
fdf9cf
cfeae6
cee9f5

Requirements
Nice to have
• minimalistic style
• easy to read and remember

```html
<!DOCTYPE html>
<html lang="en">
<head>
<meta charset="UTF-8">
<title>Mira Bloom Fitness Coaching – Business Card</title>
<link rel="stylesheet" href="https://fonts.googleapis.com/css2?family=Cinzel:wght@700&family=Crimson+Text:wght@400&family=Montserrat:wght@400;500&display=swap">
<style>
  :root {
    --backdrop: #2b2b2d;
    --card: #ffffff;
    --card-edge: #ececec;
    --pink: #e987b8;
    --pink-soft: #eea4c8;
    --ink: #1d1d1f;
    --ink-soft: #4a4a4f;
    --divider: #f4f4f4;
  }
  * { margin: 0; padding: 0; box-sizing: border-box; }
  html, body {
    width: 1200px;
    height: 997px;
    overflow: hidden;
    background: var(--backdrop);
  }
  .canvas {
    position: relative;
    width: 1200px;
    height: 997px;
  }
  .card {
    position: absolute;
    width: 640px;
    height: 366px;
    border-radius: 22px;
    overflow: hidden;
    background: var(--card);
    box-shadow: 0 12px 30px rgba(0,0,0,0.45);
  }
  .card--front { left: 280px; top: 90px; }
  .card--back  { left: 280px; top: 530px; }

  .photo-collage { display: block; width: 100%; height: 100%; }

  .identity {
    position: absolute;
    left: 0;
    top: 150px;
    width: 100%;
  }
  .identity__name {
    margin-left: 70px;
    font-family: "Cinzel", serif;
    font-weight: 700;
    font-size: 38px;
    letter-spacing: 1px;
    color: var(--pink);
    line-height: 1;
  }
  .identity__role {
    margin-left: 72px;
    margin-top: 6px;
    font-family: "Montserrat", sans-serif;
    font-size: 14px;
    letter-spacing: 5px;
    color: var(--ink-soft);
  }
  .specialty-bar {
    margin-top: 6px;
    width: 400px;
    height: 24px;
    background: var(--pink-soft);
    border-radius: 0 12px 12px 0;
    display: flex;
    align-items: center;
    padding-left: 72px;
    font-family: "Montserrat", sans-serif;
    font-weight: 500;
    font-size: 12.5px;
    color: var(--ink);
    white-space: nowrap;
  }
  .contacts {
    margin-left: 72px;
    margin-top: 16px;
    font-family: "Crimson Text", serif;
    font-size: 21px;
    color: var(--ink);
  }
  .contacts__row {
    display: flex;
    align-items: center;
    gap: 22px;
    margin-bottom: 8px;
  }
  .contact {
    display: flex;
    align-items: center;
    gap: 7px;
  }
  .contact__icon { width: 16px; height: 16px; flex: none; }
</style>
</head>
<body>
<main class="canvas">

  <section class="card card--front">
    <svg class="photo-collage" viewBox="0 0 640 366" role="img" aria-label="Collage of three diagonal photo bands showing the trainer doing a handstand, a smiling portrait, and a lunge stretch against pink and teal walls">
      <defs>
        <linearGradient id="band-top" x1="0" y1="0" x2="1" y2="0">
          <stop offset="0" stop-color="#e7a9ad"/>
          <stop offset="0.6" stop-color="#d9b8bf"/>
          <stop offset="1" stop-color="#e9e6ea"/>
        </linearGradient>
        <linearGradient id="band-mid" x1="0" y1="0" x2="1" y2="0">
          <stop offset="0" stop-color="#7b7b7e"/>
          <stop offset="0.45" stop-color="#c9a892"/>
          <stop offset="1" stop-color="#eadfdf"/>
        </linearGradient>
        <linearGradient id="band-low" x1="0" y1="0" x2="1" y2="1">
          <stop offset="0" stop-color="#d66fa3"/>
          <stop offset="0.45" stop-color="#8ec6c4"/>
          <stop offset="1" stop-color="#9fd2cf"/>
        </linearGradient>
      </defs>
      <rect width="640" height="366" fill="#ffffff"/>
      <polygon points="0,0 640,0 640,40 0,170" fill="url(#band-top)"/>
      <polygon points="0,176 640,46 640,160 0,290" fill="url(#band-mid)"/>
      <polygon points="0,296 640,166 640,366 0,366" fill="url(#band-low)"/>
    </svg>
  </section>

  <section class="card card--back">
    <div class="identity">
      <h1 class="identity__name">TESSA BROGAN</h1>
      <p class="identity__role">Personal Trainer</p>
      <p class="specialty-bar">Weight Loss • Flexibility • Mobility</p>
      <div class="contacts">
        <div class="contacts__row">
          <span class="contact">
            <svg class="contact__icon" viewBox="0 0 16 16" aria-hidden="true">
              <path d="M2 6c0-2 2-3 6-3s6 1 6 3v1h-3V5.5H5V7H2z" fill="var(--pink)"/>
              <rect x="3" y="8" width="10" height="6" rx="1.5" fill="var(--pink)"/>
              <circle cx="8" cy="11" r="1.6" fill="#fff"/>
            </svg>
            07700218493
          </span>
          <span class="contact">
            <svg class="contact__icon" viewBox="0 0 16 16" aria-hidden="true">
              <rect x="1" y="3" width="14" height="10" rx="1" fill="var(--pink)"/>
              <path d="M1.5 3.5 8 9l6.5-5.5" fill="none" stroke="#fff" stroke-width="1.3"/>
            </svg>
            tessa.brogan@quellmail.com
          </span>
        </div>
        <div class="contacts__row">
          <span class="contact">
            <svg class="contact__icon" viewBox="0 0 16 16" aria-hidden="true">
              <rect x="2" y="2" width="12" height="12" rx="2" fill="var(--pink)"/>
            </svg>
            photoreel.net/Mira_Bloom
          </span>
        </div>
      </div>
    </div>
  </section>

</main>
</body>
</html>
```